Investment company needing business card

We are wanting a business card which looks sharp and easy on the eye. We are thinking of having a business card with the logo embossed on it, to really make it stand out. We will only have a small amount of information of the business card, person's name, position, email address and phone number

Contact Information for Business Card

Danielle Frost
Executive Assistant
+64 21 473 5162
danielf@harwickpartners.co.nz

Requirements
Must have
• Embossed logo
Should not have
• Not to be busy

```html
<!DOCTYPE html>
<html lang="en">
<head>
<meta charset="utf-8">
<title>Harwick Partners – Business Card</title>
<link rel="stylesheet" href="https://fonts.googleapis.com/css2?family=Roboto:wght@400;500&display=swap">
<style>
  :root {
    --backdrop: #2b2b2d;
    --card: #1e1f20;
    --card-edge: #262729;
    --green: #2fb777;
    --white: #f2f2f2;
    --emboss: #343537;
    --emboss-mark: #27302b;
  }
  * { box-sizing: border-box; margin: 0; padding: 0; }
  html, body { width: 1200px; height: 900px; overflow: hidden; }
  body {
    background: var(--backdrop);
    font-family: "Roboto", Arial, sans-serif;
    position: relative;
  }
  .card {
    position: absolute;
    left: 250px;
    width: 700px;
    height: 400px;
    background: linear-gradient(160deg, var(--card-edge), var(--card));
    border-radius: 4px;
    overflow: hidden;
  }
  .card--front { top: 40px; }
  .card--back { top: 470px; }

  /* Front: embossed name */
  .front-mark {
    position: absolute;
    left: 300px; top: 110px;
    width: 180px; height: 180px;
    background: var(--emboss-mark);
  }
  .front-brand {
    position: absolute;
    left: 0; right: 0; top: 168px;
    text-align: center;
    font-size: 50px;
    font-weight: 500;
    letter-spacing: 3px;
    color: var(--emboss);
    text-transform: uppercase;
  }

  /* Back: logo lockup */
  .brand {
    position: absolute;
    left: 60px; top: 50px;
    display: flex; align-items: center; gap: 14px;
  }
  .brand-square { width: 44px; height: 44px; background: var(--green); }
  .brand-name {
    font-size: 30px; font-weight: 500; letter-spacing: 2px;
    color: var(--green); text-transform: uppercase;
  }

  .divider {
    position: absolute;
    left: 70px; right: 60px; top: 252px;
    height: 2px; background: var(--green);
  }
  .person {
    position: absolute;
    right: 60px; top: 196px;
    text-align: right;
  }
  .person-name {
    font-size: 36px; font-weight: 400; letter-spacing: 1px;
    color: var(--green); text-transform: uppercase; line-height: 1;
  }
  .person-role {
    margin-top: 22px;
    font-size: 19px; color: var(--white);
  }
  .edge-bar {
    position: absolute; right: 22px; top: 232px;
    width: 4px; height: 64px; background: var(--white);
  }
  .edge-block {
    position: absolute; right: 0; top: 232px;
    width: 18px; height: 64px; background: var(--green);
  }

  .contact {
    position: absolute;
    left: 70px; top: 290px;
    list-style: none;
  }
  .contact li {
    display: flex; align-items: center; gap: 14px;
    font-size: 18px; color: var(--white);
    line-height: 28px;
  }
  .contact svg { width: 13px; height: 13px; flex: none; }
</style>
</head>
<body>

<section class="card card--front">
  <div class="front-mark"></div>
  <div class="front-brand">Harwick Partners</div>
</section>

<section class="card card--back">
  <div class="brand">
    <span class="brand-square"></span>
    <span class="brand-name">Harwick Partners</span>
  </div>

  <div class="person">
    <div class="person-name">Danielle Frost</div>
    <div class="person-role">Executive Assistant</div>
  </div>
  <div class="divider"></div>
  <div class="edge-bar"></div>
  <div class="edge-block"></div>

  <ul class="contact">
    <li>
      <svg viewBox="0 0 16 16" aria-hidden="true"><path d="M4 1l2.5 3-1.5 2c1 2 3 4 5 5l2-1.5 3 2.5-1.5 2C8 15 1 8 2 3z" fill="#2fb777"/></svg>
      +64 21 473 5162
    </li>
    <li>
      <svg viewBox="0 0 16 16" aria-hidden="true"><rect x="1" y="3" width="14" height="10" fill="none" stroke="#2fb777" stroke-width="1.5"/><path d="M1 3l7 6 7-6" fill="none" stroke="#2fb777" stroke-width="1.5"/></svg>
      danielf@harwickpartners.co.nz
    </li>
    <li>
      <svg viewBox="0 0 16 16" aria-hidden="true"><circle cx="8" cy="8" r="6.5" fill="none" stroke="#2fb777" stroke-width="1.5"/><path d="M1.5 8h13M8 1.5c-3 3-3 10 0 13M8 1.5c3 3 3 10 0 13" fill="none" stroke="#2fb777" stroke-width="1.2"/></svg>
      www.harwickpartners.co.nz
    </li>
  </ul>
</section>

</body>
</html>
```